Facial Tissue Brand Logo and Design

We would like you to design a Logo for the Facial Tissue Brand "Velora" along with the box design. The pack should indicate the pack size (150 x 2 ply). Also our company logo should be present (attached) along with a barcode. The box size dimensions should be 210mm (L) x 110mm (W) x 70mm (H). We are open to all kinds of nice designs which are attractive but not overdone. Happy designing!

UPDATE:
We appreciate the designs so far... but would also love to see more options in a simple and elegent design style that would look good on a table... please see attached below links for reference purpose:

www.pictovault-example.com/image-photo/cleaning-wipes-isolated-on-white-257770819

www.pictovault-example.com/image-photo/cleaning-wipes-isolated-on-white-155326937

www.pictovault-example.com/image-photo/delicate-female-hands-pulling-tissue-out-1330426586

Happy desgining!

We appreciate the designs so far.. but would like to to see some more options.

```html
<!DOCTYPE html>
<html lang="en">
<head>
<meta charset="utf-8">
<title>Velora Facial Tissue – Box Dieline</title>
<link href="https://fonts.googleapis.com/css2?family=Marcellus&family=Raleway:wght@400;500&display=swap" rel="stylesheet">
<style>
  :root {
    --brand-red: #ef4b51;
    --paper: #ffffff;
    --pattern-light: #fbf6ea;
    --pattern-warm: #f3e3c4;
    --pattern-mint: #d9efe6;
    --fold-line: #5a5a5a;
    --text-light: #ffffff;
  }
  html, body {
    margin: 0;
    width: 750px;
    height: 1200px;
    overflow: hidden;
    background: var(--paper);
  }
  .dieline {
    position: absolute;
    left: 12px;
    top: 148px;
    width: 725px;
    height: 904px;
  }
  .brand-name { font-family: "Marcellus", serif; fill: var(--text-light); }
  .brand-sub { font-family: "Raleway", sans-serif; fill: var(--text-light); font-weight: 500; }
  .web-address { font-family: "Raleway", sans-serif; fill: var(--text-light); letter-spacing: 1px; }
  .company-name { font-family: "Raleway", sans-serif; font-weight: 500; fill: var(--text-light); }
  .pack-size { font-family: "Raleway", sans-serif; fill: var(--text-light); }
  .panel-red { fill: var(--brand-red); }
  .panel-pattern { fill: url(#patternTone); }
  .fold { stroke: var(--fold-line); stroke-width: 0.8; fill: none; }
</style>
</head>
<body>
<svg class="dieline" viewBox="213 927 853 1063" xmlns="http://www.w3.org/2000/svg">
  <defs>
    <linearGradient id="patternTone" x1="0" y1="0" x2="1" y2="1">
      <stop offset="0" stop-color="var(--pattern-light)"/>
      <stop offset="0.5" stop-color="var(--pattern-warm)"/>
      <stop offset="1" stop-color="var(--pattern-mint)"/>
    </linearGradient>
  </defs>

  <!-- Patterned panels -->
  <g role="img" aria-label="Repeating pattern of small red, yellow, mint and beige triangles on white">
    <rect class="panel-pattern" x="243" y="927" width="99" height="198"/>
    <rect class="panel-pattern" x="937" y="927" width="100" height="198"/>
    <rect class="panel-pattern" x="342" y="997" width="595" height="128"/>
    <rect class="panel-pattern" x="213" y="1133" width="129" height="297"/>
    <rect class="panel-pattern" x="342" y="1125" width="595" height="312"/>
    <rect class="panel-pattern" x="937" y="1133" width="129" height="297"/>
    <rect class="panel-pattern" x="243" y="1437" width="99" height="200"/>
    <rect class="panel-pattern" x="937" y="1437" width="100" height="200"/>
    <rect class="panel-pattern" x="342" y="1437" width="595" height="128"/>
  </g>

  <!-- Back top band with company name -->
  <g class="back-band">
    <rect class="panel-red" x="342" y="927" width="595" height="70"/>
    <text class="company-name" x="880" y="970" font-size="11" text-anchor="end">Norvane Trading</text>
    <rect x="892" y="956" width="18" height="18" fill="var(--text-light)"/>
  </g>

  <!-- Top panel: brand oval and pack size -->
  <g class="top-panel">
    <ellipse class="panel-red" cx="640" cy="1281" rx="195" ry="72"/>
    <text class="brand-name" x="640" y="1284" font-size="52" text-anchor="middle">Velora</text>
    <text class="brand-sub" x="640" y="1317" font-size="20" text-anchor="middle">Facial Tissue</text>

    <g class="pack-badge">
      <rect class="panel-red" x="838" y="1370" width="89" height="58"/>
      <text class="pack-size" x="865" y="1423" font-size="52" text-anchor="middle" font-weight="500">2</text>
      <text class="pack-size" x="904" y="1392" font-size="17" text-anchor="middle">ply</text>
      <line x1="889" y1="1398" x2="919" y2="1398" stroke="var(--text-light)" stroke-width="1"/>
      <text class="pack-size" x="904" y="1415" font-size="15" text-anchor="middle" font-weight="500">150</text>
      <text class="pack-size" x="904" y="1423" font-size="6" text-anchor="middle">sheets</text>
    </g>
  </g>

  <!-- Front band -->
  <g class="front-band">
    <rect class="panel-red" x="342" y="1565" width="595" height="72"/>
    <text class="brand-name" x="430" y="1600" font-size="30" text-anchor="middle">Velora</text>
    <text class="brand-sub" x="430" y="1619" font-size="12" text-anchor="middle">Facial Tissue</text>
  </g>

  <!-- Bottom panel and tabs -->
  <g class="bottom-panel">
    <path class="panel-red" d="M342 1637 H937 V1940 L918 1978 Q912 1990 898 1990 H382 Q368 1990 362 1978 L342 1940 Z"/>
    <path class="panel-red" d="M292 1637 H342 V1940 H292 V1897 H243 V1685 H292 Z"/>
    <path class="panel-red" d="M937 1637 H987 V1685 H1037 V1897 H987 V1940 H937 Z"/>

    <text class="brand-name" x="640" y="1797" font-size="46" text-anchor="middle">Velora</text>
    <text class="brand-sub" x="640" y="1826" font-size="18" text-anchor="middle">Facial Tissue</text>
    <text class="web-address" x="640" y="1902" font-size="13" text-anchor="middle">www.norvanetrading-example.com</text>

    <g transform="translate(308 1790) rotate(-90)">
      <text class="brand-name" x="0" y="0" font-size="34" text-anchor="middle">Velora</text>
    </g>
    <g transform="translate(328 1790) rotate(-90)">
      <text class="brand-sub" x="0" y="0" font-size="11" text-anchor="middle">Facial Tissue</text>
    </g>

    <g transform="translate(995 1790) rotate(90)">
      <text class="company-name" x="0" y="0" font-size="11" text-anchor="middle">Norvane Trading</text>
      <rect x="-62" y="-12" width="12" height="12" fill="var(--text-light)"/>
    </g>
  </g>

  <!-- Fold lines -->
  <g class="folds">
    <line class="fold" x1="342" y1="927" x2="342" y2="1940"/>
    <line class="fold" x1="937" y1="927" x2="937" y2="1940"/>
    <line class="fold" x1="342" y1="1125" x2="937" y2="1125"/>
    <line class="fold" x1="342" y1="1133" x2="937" y2="1133"/>
    <line class="fold" x1="342" y1="1430" x2="937" y2="1430"/>
    <line class="fold" x1="342" y1="1437" x2="937" y2="1437"/>
    <line class="fold" x1="342" y1="1637" x2="937" y2="1637"/>
    <line class="fold" x1="342" y1="1940" x2="937" y2="1940"/>
  </g>
</svg>
</body>
</html>
```